Stationery Design Project for Nimbora, Chicago

Nimbora, a street parking application which helps car drivers find a street parking spot by offering an ideal path along which to look for parking. This path is calculated by our algorithm based on data (e.g. historical data, baseball games schedule, etc.). Along this path the driver will find a spot and will also save 70% of the search time. Customer we target is reg. between 21 and 45 yo.

We envision something young, fresh, bright and original. Slightly abstract maybe. It should represent the idea and elements of finding street parking in the city, e.g. car(s), parking spot, people, city, etc. (just ideas!).

Logo is attached.

Requirement:
- Business Cards (2 Sided Full Color CMYK)
- Letterhead (1 Sided Full Color CMYK)
- Envelope (1 Sided Full Color CMYK)
- Sticker (1 Sided Full Color CMYK), round with a 2inch diameter.

Reason: We're starting to get more and more designs and need more time to look into all of them. Very exciting!! Thanks to everybody!

Hi all, we're in the process of selecting our favs. Though choices!!! Really good submissions. Will keep you posted and sorry for the delay.

Target Market(s)

Car drivers and owners between 21 and 45

Industry/Entity Type

Parking

Requirements
Must have
• Sticker should be round and include company URL nimbora.com and the new logo which we will attach soon.
Should not have
• Should not be too serious or boring.

```html
<!DOCTYPE html>
<html lang="en">
<head>
<meta charset="utf-8">
<title>Nimbora Business Card</title>
<link rel="stylesheet" href="https://fonts.googleapis.com/css2?family=Open+Sans:wght@400;600;700&display=swap">
<style>
  :root {
    --bg: #e9e6e2;
    --card: #050505;
    --ink: #ffffff;
    --brand-blue: #2a7cc7;
    --ring: #d9d9d9;
  }
  * { margin: 0; padding: 0; box-sizing: border-box; }
  html, body { width: 1200px; height: 668px; overflow: hidden; background: var(--bg); }
  body { font-family: "Open Sans", sans-serif; color: var(--ink); position: relative; }

  .card {
    position: absolute;
    top: 184px;
    width: 520px;
    height: 300px;
    background: var(--card);
    border-radius: 30px;
    box-shadow: 0 6px 18px rgba(0,0,0,0.25);
    overflow: hidden;
  }
  .card--front { left: 45px; }
  .card--back { left: 635px; }

  /* Front */
  .brand {
    position: absolute;
    left: 48px;
    top: 122px;
    display: flex;
    align-items: center;
    gap: 12px;
  }
  .brand__dot {
    width: 58px; height: 58px;
    border-radius: 50%;
    background: var(--brand-blue);
    border: 3px solid var(--ring);
  }
  .brand__name {
    font-size: 38px;
    font-weight: 600;
    letter-spacing: 0.5px;
    color: var(--ink);
  }
  .web-band {
    position: absolute;
    left: 283px;
    top: 60px;
    width: 24px;
    height: 178px;
    background: var(--brand-blue);
    border-left: 3px solid var(--ink);
    display: flex;
    align-items: center;
    justify-content: center;
  }
  .web-band__url {
    writing-mode: vertical-rl;
    transform: rotate(180deg);
    font-size: 12px;
    letter-spacing: 0.6px;
    color: var(--ink);
    white-space: nowrap;
  }
  .contact {
    position: absolute;
    left: 326px;
    top: 58px;
  }
  .contact__name { font-size: 17px; font-weight: 700; line-height: 1.2; }
  .contact__title { font-size: 12px; margin-top: 6px; }
  .contact__list { list-style: none; margin-top: 14px; }
  .contact__list li {
    font-size: 13px;
    line-height: 18px;
    display: flex;
    align-items: center;
    gap: 5px;
  }
  .contact__list svg { width: 10px; height: 10px; fill: var(--ink); flex: none; }
  .contact__address { font-size: 13px; line-height: 17px; margin-top: 14px; }

  /* Back */
  .mark {
    position: absolute;
    left: 50%;
    top: 52px;
    width: 150px; height: 150px;
    margin-left: -75px;
    border-radius: 50%;
    background: var(--brand-blue);
    box-shadow: 0 0 0 5px var(--card), 0 0 0 9px var(--ring);
  }
  .back__url {
    position: absolute;
    left: 0; right: 0;
    bottom: 34px;
    text-align: center;
    font-size: 26px;
    font-weight: 700;
    letter-spacing: 4px;
  }
</style>
</head>
<body>
  <section class="card card--front">
    <div class="brand">
      <span class="brand__dot"></span>
      <span class="brand__name">nimbora</span>
    </div>
    <div class="web-band"><span class="web-band__url">www.nimbora.com</span></div>
    <div class="contact">
      <p class="contact__name">Your Name</p>
      <p class="contact__title">Title</p>
      <ul class="contact__list">
        <li><svg viewBox="0 0 10 10"><path d="M2 0.5 L3.8 2.6 L2.9 3.7 Q4 6 6.3 7.1 L7.4 6.2 L9.5 8 L8.3 9.5 Q3.5 9 0.5 1.7 Z"/></svg>123-456-789</li>
        <li><svg viewBox="0 0 10 10"><path d="M2.5 0 H7.5 V10 H2.5 Z M3.4 1 V7.5 H6.6 V1 Z"/></svg>123-456-789</li>
        <li><svg viewBox="0 0 10 10"><path d="M0 2 H10 V8.5 H0 Z M0.8 2.6 L5 5.6 L9.2 2.6" stroke="#050505" stroke-width="0.7"/></svg>info@nimbora.com</li>
      </ul>
      <p class="contact__address">Complex name, Street name<br>City, State, zip code</p>
    </div>
  </section>

  <section class="card card--back">
    <div class="mark"></div>
    <p class="back__url">www.nimbora.com</p>
  </section>
</body>
</html>
```